Create a book cover for brimvale QTR

We are looking for a designer to design a cover for a log book in two versions. The two versions only have a slight difference in page count and text, other than that, it is one design.

The main color is blue. No black, no white except book title and other text. The cover must closely relate to the interior pages provided in the attachment. The style should be simple and modern, no old school graphics and fonts. Apply color psychology in the design. Please be creative and you are allowed to use download templates and graphic elements, but you must provide commercial licenses.

Here are the basic information of the book:
1. Book title: MOTOR UPKEEP TRACKING JOURNAL
2. Book size: 6x9 inches
3. Page count: 61 (version 1) and 73 (version 2)
4. Platform: brimvale qtr

Requirement for version 1:
1. Front cover: book title
2. Spine: no book title and author name
3. Back cover: text on the top and pen name logo on the bottom middle
4. Back cover text:
• Your essential tool for tracking vehicle health and maintenance
• Dedicated sections for maintenance schedules and repair history
• Track up to 30 maintenance schedules and repair history
• Easy-to-use tables and clear layouts
• Perfect for all car owners, from enthusiasts to everyday drivers

We hope it helps you keep your vehicle in excellent condition. Please take a moment to leave a positive review on Brimvale and share your experience if you find it helpful. Thank you!

Requirement for version 2:
1. Front cover: book title ,text "COLOR PAGES"
4. Back cover text:
• Track up to 36 maintenance schedules and repair history

Export:
1. Cover design in PDF and editable file format.
2. Sources/Commercial licenses for everything you did not create by yourself including fonts.

```html
<!DOCTYPE html>
<html lang="en">
<head>
<meta charset="utf-8">
<title>Motor Upkeep Tracking Journal — Cover Spread</title>
<link rel="stylesheet" href="https://fonts.googleapis.com/css2?family=Barlow+Semi+Condensed:wght@300;400&display=swap">
<style>
  :root {
    --stage: #1b1c1a;
    --navy-deep: #1c2438;
    --navy-mid: #22364a;
    --navy-front: #2a3546;
    --navy-spine: #2c3643;
    --ink-light: #d9dde3;
    --ink-soft: #aab3bf;
    --rule: #8d97a4;
  }
  * { box-sizing: border-box; margin: 0; padding: 0; }
  html, body { width: 1200px; height: 900px; overflow: hidden; }
  body {
    background: var(--stage);
    font-family: "Barlow Semi Condensed", "Arial Narrow", sans-serif;
    color: var(--ink-light);
  }
  .cover-spread {
    position: absolute;
    left: 100px; top: 90px;
    width: 1000px; height: 720px;
    display: flex;
  }
  .back-cover {
    width: 480px; height: 100%;
    background: linear-gradient(160deg, var(--navy-deep) 0%, var(--navy-mid) 45%, var(--navy-deep) 100%);
    position: relative;
  }
  .spine {
    width: 40px; height: 100%;
    background: var(--navy-spine);
    border-left: 1px solid rgba(0,0,0,0.25);
    border-right: 1px solid rgba(0,0,0,0.35);
    box-shadow: inset 6px 0 8px rgba(0,0,0,0.18), inset -6px 0 8px rgba(0,0,0,0.22);
  }
  .front-cover {
    width: 480px; height: 100%;
    background: linear-gradient(150deg, #2e394a 0%, var(--navy-front) 50%, #252e3d 100%);
    position: relative;
  }
  .feature-block {
    position: absolute;
    left: 42px; right: 42px; top: 118px;
    text-align: left;
  }
  .short-rule {
    width: 62px; height: 1px;
    background: var(--rule);
    margin: 0 auto;
  }
  .feature-list {
    list-style: none;
    margin: 12px 0;
    font-size: 12.5px;
    font-weight: 300;
    line-height: 1.45;
    color: var(--ink-soft);
    letter-spacing: 0.2px;
  }
  .feature-list li::before { content: "· "; }
  .pen-name {
    position: absolute;
    left: 0; right: 0; bottom: 52px;
    display: flex; align-items: center; justify-content: center; gap: 8px;
    font-size: 13px; font-weight: 400; letter-spacing: 2px;
    color: var(--ink-light);
  }
  .pen-name-dot {
    width: 10px; height: 10px; border-radius: 50%;
    background: var(--ink-soft);
  }
  .title-block {
    position: absolute;
    left: 34px; right: 30px; top: 250px;
    text-align: center;
  }
  .title-main {
    font-size: 40px;
    font-weight: 300;
    letter-spacing: 1px;
    line-height: 1;
    color: var(--ink-light);
    white-space: nowrap;
  }
  .title-rule {
    width: 70px; height: 1px;
    background: var(--rule);
    margin: 12px auto 8px;
  }
  .title-sub {
    font-size: 15px;
    font-weight: 300;
    letter-spacing: 5px;
    color: var(--ink-soft);
  }
</style>
</head>
<body>
  <main class="cover-spread">
    <section class="back-cover">
      <div class="feature-block">
        <div class="short-rule"></div>
        <ul class="feature-list">
          <li>Your essential tool for tracking vehicle health and maintenance</li>
          <li>Dedicated sections for maintenance schedules and repair history</li>
          <li>Track up to 30 maintenance schedules and repair history</li>
          <li>Easy-to-use tables and clear layouts</li>
          <li>Perfect for all car owners, from enthusiasts to everyday drivers</li>
        </ul>
        <div class="short-rule"></div>
      </div>
      <div class="pen-name">
        <span class="pen-name-dot"></span>
        <span>TOBIAS VARNE</span>
      </div>
    </section>
    <div class="spine"></div>
    <section class="front-cover">
      <div class="title-block">
        <h1 class="title-main">MOTOR UPKEEP TRACKING</h1>
        <div class="title-rule"></div>
        <p class="title-sub">JOURNAL</p>
      </div>
    </section>
  </main>
</body>
</html>
```